Luxury Wine Label for New Startup Winery

We need a wine label for our new winery startup. We have worked with a local designer but do not feel the resulting label / logo have the elevation required to present our brand as a luxury wine. Our winery is called "Quailbrook Vineyards" and we are focused on extremely high quality hand crafted artisan and estate wines from the Pacific Northwest.
We would like to see designs that utilize a tree line, or other imagery that represents the "Quailbrook" part of our company name. Another interesting feature could be wood grain.
A logo will be required based on your design so please design with this in mind:
This logo should be consistent with the wine bottle label design, and should be representative of our high end exclusive wine while giving a sense of place (Oregon/ Pacific Northwest.)
I will supply an image of the design we received from our local designer, PLEASE NOTE: in general we do like wood grain and tree line concepts but feel the execution was poorly done.
ATTN: Logo design should be suitable for use on: Bottles (Red wine/rose/white wine), Bussiness cards, vehicle signage, business signage, etc
P.S.:
If you have a design that is not outside the box we are still interested in seeing it.
Label is for a burgundy style bottle with a label height of 3.5 - 4" and a width of 3.5-4"
any label <= 4"x4" and >=3.5"x3.5" will be acceptable:
HOWEVER Width should be greater than or equal to height due to the bottle format
Target Market(s)
Wine enthusiasts with adequate discretionary budgets to afford $100 bottles of wine.
Industry/Entity Type
Wine / Winery
Requirements
Must have
- A sense of luxury, a feel of exclusivity, and a theme consistent with our product and brand name
Nice to have
- Tree line, wood grain or other wood themes. Serif fonts
Should not have
- anything cheesy, off topic, hard to read script fonts or anything that makes the label hard to read from a few feet away or too busy

```html
<!DOCTYPE html>
<html lang="en">
<head>
<meta charset="utf-8">
<title>Quailbrook Vineyards – Syrah Label</title>
<link rel="stylesheet" href="https://fonts.googleapis.com/css2?family=Crimson+Text:wght@400;700&family=Great+Vibes&display=swap">
<style>
  :root {
    --canvas-bg: #ffffff;
    --label-black: #000000;
    --frame-grey: #9c9c9c;
    --gold-dark: #a47a1f;
    --gold-mid: #d6ae52;
    --gold-light: #f3dc9a;
    --wood-dark: #4a2a17;
    --wood-mid: #7a4a2c;
    --wood-light: #95613d;
  }
  * { margin: 0; padding: 0; box-sizing: border-box; }
  html, body {
    width: 1200px;
    height: 848px;
    overflow: hidden;
    background: var(--canvas-bg);
  }
  .canvas {
    position: relative;
    width: 1200px;
    height: 848px;
  }
  .label {
    position: absolute;
    left: 260px;
    top: 64px;
    width: 788px;
    height: 833px;
    transform: scale(0.863);
    transform-origin: top left;
  }
  .label-art {
    position: absolute;
    inset: 0;
    width: 788px;
    height: 833px;
  }
  .gold-text {
    background: linear-gradient(90deg, var(--gold-dark) 0%, var(--gold-mid) 25%, var(--gold-light) 50%, var(--gold-mid) 72%, var(--gold-dark) 100%);
    -webkit-background-clip: text;
    background-clip: text;
    color: transparent;
  }
  .brand-name {
    position: absolute;
    left: 0;
    width: 788px;
    text-align: center;
    font-family: "Crimson Text", serif;
    font-weight: 400;
    line-height: 1;
    white-space: nowrap;
  }
  .brand-name--first { top: 296px; font-size: 100px; }
  .brand-name--second { top: 368px; font-size: 86px; }
  .region {
    position: absolute;
    left: 0;
    top: 508px;
    width: 788px;
    text-align: center;
    font-family: "Crimson Text", serif;
    font-weight: 700;
    font-size: 46px;
    letter-spacing: 1px;
    line-height: 1;
  }
  .varietal {
    position: absolute;
    left: 0;
    top: 682px;
    width: 788px;
    text-align: center;
    font-family: "Great Vibes", cursive;
    font-size: 104px;
    line-height: 1;
  }
  .vintage-line {
    position: absolute;
    left: 0;
    top: 796px;
    width: 788px;
    text-align: center;
    font-family: "Crimson Text", serif;
    font-weight: 700;
    font-size: 21px;
    letter-spacing: 1.5px;
    line-height: 1;
  }
</style>
</head>
<body>
<main class="canvas">
  <section class="label">
    <svg class="label-art" viewBox="0 0 788 833" xmlns="http://www.w3.org/2000/svg">
      <defs>
        <linearGradient id="goldSweep" x1="0" y1="0" x2="1" y2="0">
          <stop offset="0" stop-color="#a47a1f"/>
          <stop offset="0.3" stop-color="#d6ae52"/>
          <stop offset="0.5" stop-color="#f3dc9a"/>
          <stop offset="0.75" stop-color="#c99a3c"/>
          <stop offset="1" stop-color="#a47a1f"/>
        </linearGradient>
        <linearGradient id="woodTone" x1="0" y1="0" x2="1" y2="0.2">
          <stop offset="0" stop-color="#7a4a2c"/>
          <stop offset="0.35" stop-color="#95613d"/>
          <stop offset="0.65" stop-color="#6e4026"/>
          <stop offset="1" stop-color="#4a2a17"/>
        </linearGradient>
      </defs>

      <path class="label-body" fill="#000000"
            d="M0,637 V250 C30,140 240,60 410,0 C560,40 740,100 788,175 V637 Z"/>

      <path class="treeline-art" role="img" aria-label="Gold forest tree line silhouette with two birds in flight"
            fill="url(#goldSweep)"
            d="M25,285 C40,175 250,95 410,28 C560,62 720,112 762,182 C610,238 460,252 330,243 C205,236 95,250 25,285 Z"/>

      <path class="label-frame" fill="none" stroke="#9c9c9c" stroke-width="2.5"
            d="M25,320 V612 H762 V210"/>

      <rect class="wood-band" role="img" aria-label="Walnut wood grain band"
            x="0" y="662" width="788" height="171" fill="url(#woodTone)"/>

      <path class="varietal-frame" fill="none" stroke="#d6ae52" stroke-width="2"
            d="M250,808 H25 V687 H762 V808 H540"/>
    </svg>

    <h1 class="brand-name brand-name--first gold-text">Quailbrook</h1>
    <p class="brand-name brand-name--second gold-text">Vineyards</p>
    <p class="region gold-text">WILLAMETTE VALLEY</p>
    <p class="varietal gold-text">Syrah</p>
    <p class="vintage-line gold-text">ESTATE | 2023 | GROWN</p>
  </section>
</main>
</body>
</html>
```